Hurricane Damage Public Adjuster Billboard

I have created several projects with you and have several great designs. I need to format them into a Billboard for upcoming Hurricane Season. Need done in a month. Im also in process of getting an eye catching and easy to remember 800# Vanity phone number like Call 800-Stormsafe or 800- Need Fix? My included past Craft Huddle projects will give you an idea of what colors, schemes, and designs I gravitate towards. 3 past Design projects were 1) 2 Logos where I picked the 1st place and the 2nd place and 2) Index Card where I picked the winner as the Index Card and the 2nd place as a Post Card. Point is, I will pick and pay for 2 winners if they're good. This should help to sweeten the pot. Also, please look at my website for ideas that I like:

www.TheClaimKeeperGroup.com
I want people to feel that I am the best and highest. Level.

I've been getting a lot of quick half effort designs basically cut & pasting my previous projects. Please don't rush and take your time to be creative. A an example, my Biggest Competitor is Vesta Public Adjusting. Their colors are Black and Gold while mine are Blue, White, and Black with a highlight of Orange if possible. I JUST imported a picture of their BillBoard. I need mine better and BLOW AWAY THEIRS. Terms like "Don't be Victimized Twice ?, Don't let the Hurricane Ruin your Life?". "Get Fairly Paid & Move On" "Our Clients Claims are VIP?
Updates

I'm getting a lot of quick half effort ones. I'd rather you take your time and really put some thoughts and effort into it. My Biggest Competitor is Vesta Public Adjusting. They have black & gold colors, while I have Blue, Black, and white.

It needs to blow theirs away. I have imported their Billboard for comparative purposes.

Guy's,
I'll make it easier for you in what I'm looking for. Please look at the Vesta Billboard picture attached.

1) Put my "Blue Shield" to the left, replacing their logo
2) change color patterns from their (Black, Gold, White) to my color schemes of (Black, Blue, White)
3) I want to see my name where their is:

THE
Claim Keeper's Group
EXPERT & LOCAL Public Adjusters
"FOR THE POLICYHOLDER!!"

4) to the right, add the A+Rated logo and QRS+ Accredited logo, 5 Star Zorbix Rated logo, 5 Start PORCHLINE Highly Rated logo, etc..

5) the right side is where you can be creative as I will not have a picture of me there.

"20+ Years of Experience, Recovering Millions for our VIP Clients"

"Your Best, Locally-Based Private Adjuster & Advocate'
"FOR THE POLICYHOLDER!!"

"Don't be victimized Twice!!"

"Don't let the Hurricane Ruin Your Life!!"

This should really help. Also, refer to my website, maybe a couple testimonial fillers?

Thanks all,

marcus@TheClaimKeeperGroup.com

Just imported a few awards that would look great to the right side with all the other 5 Star Ratings and accolades.
This right section could be titled like zmy Website:

5 Star Reviews, Ratings & Awards:
4-5 Logos underneath?

Target Market(s)

Coastal place where a Hurricane 🌀 🌀 Hits

Industry/Entity Type

Hurricane Public Insurance Adjuster

Font styles to use
Sans Serif
Other font styles liked:
• Zurich fonts

Colors
0054AA
0677BA
7BADD7
CADEEF
E8F1F8
EE7325
F08F49
F5BC92
FAE3D3
FDF4ED

Requirements
Must have
• Use my past project logos, colors, and schemes to create eye grabbing BillBoard
Nice to have
Should not have
• Not be too busy, must be Easy to Read, Eye Catchy

```html
<!DOCTYPE html>
<html lang="en">
<head>
<meta charset="utf-8">
<title>Claim Keeper's Group – Billboard</title>
<link rel="stylesheet" href="https://fonts.googleapis.com/css2?family=Cinzel:wght@500&family=EB+Garamond:wght@700&family=Playfair+Display:ital,wght@1,900&family=Montserrat:wght@700;800&display=swap">
<style>
  :root {
    --page: #d3d7dd;
    --ink: #1b1b1b;
    --white: #ffffff;
    --sky: #00b4ee;
    --sky-deep: #0096dd;
    --shield-blue: #00a6e2;
    --orange: #d67f2a;
    --phone-orange: #d2711f;
    --rating-red: #e8202a;
    --badge-blue: #0a5f9c;
    --navy: #1f4e7a;
    --review-blue: #3b78e7;
    --star-gold: #f7b500;
    --porch-green: #7cc400;
  }
  * { margin: 0; padding: 0; box-sizing: border-box; }
  html, body { width: 1190px; height: 1200px; overflow: hidden; background: var(--page); }
  .billboard {
    position: absolute; left: 20px; top: 408px;
    width: 1150px; height: 383px;
    background: var(--white);
    box-shadow: 0 14px 24px rgba(0,0,0,.22);
    overflow: hidden;
  }
  .billboard__bands { position: absolute; inset: 0; width: 100%; height: 100%; }
  .brand-mark {
    position: absolute; left: 42px; top: 30px;
    width: 226px; height: 226px; border-radius: 50%;
    background: var(--shield-blue);
  }
  .brand-name {
    position: absolute; left: 300px; width: 560px; text-align: center;
    font-family: "Cinzel", serif; font-weight: 500; color: var(--white);
  }
  .brand-name__lead { top: 36px; font-size: 47px; line-height: 56px; letter-spacing: 1px; }
  .brand-name__tail { top: 98px; font-size: 33px; line-height: 38px; letter-spacing: 12px; }
  .rule { position: absolute; top: 118px; height: 3px; width: 108px; background: var(--shield-blue); }
  .rule--left { left: 330px; }
  .rule--right { left: 762px; }
  .service-line {
    position: absolute; left: 300px; width: 560px; top: 156px; text-align: center;
    font-family: "EB Garamond", serif; font-weight: 700; font-size: 38px; line-height: 44px;
    color: var(--white);
  }
  .promise {
    position: absolute; left: 290px; width: 580px; top: 212px; text-align: center;
    font-family: "Playfair Display", serif; font-style: italic; font-weight: 900;
    font-size: 40px; line-height: 52px; color: var(--orange); letter-spacing: -1px;
  }
  .phone-icon { position: absolute; left: 29px; top: 306px; width: 60px; height: 60px; }
  .phone-number {
    position: absolute; left: 106px; top: 308px;
    font-family: "Montserrat", sans-serif; font-weight: 800; font-size: 47px; line-height: 56px;
    color: var(--white); letter-spacing: -1.5px;
  }
  .divider { position: absolute; left: 547px; top: 302px; width: 2px; height: 69px; background: var(--white); }
  .award {
    position: absolute; left: 575px; width: 256px; top: 311px; text-align: center;
    font-family: "Montserrat", sans-serif; font-weight: 800; font-size: 22px; line-height: 26px;
    color: var(--white);
  }
  .ratings { position: absolute; left: 917px; width: 220px; top: 0; height: 100%; text-align: center; font-family: "Montserrat", sans-serif; }
  .ratings__grade { position: absolute; top: 34px; width: 100%; font-weight: 700; font-size: 40px; line-height: 48px; color: var(--rating-red); letter-spacing: -.5px; }
  .ratings__badge {
    position: absolute; left: 8px; top: 108px; width: 205px; height: 78px;
    border: 2px solid var(--badge-blue); border-radius: 9px; overflow: hidden; background: var(--white);
  }
  .ratings__badge::after { content: ""; position: absolute; right: 0; top: 0; bottom: 0; width: 136px; background: var(--badge-blue); }
  .ratings__badge-note { position: absolute; top: 194px; width: 100%; font-weight: 700; font-size: 15px; line-height: 18px; color: var(--navy); }
  .ratings__review { position: absolute; top: 222px; width: 100%; font-weight: 700; font-size: 46px; line-height: 56px; color: var(--review-blue); letter-spacing: -1px; }
  .ratings__stars { position: absolute; top: 283px; left: 50%; transform: translateX(-50%); width: 114px; height: 20px; }
  .ratings__neighbors { position: absolute; top: 314px; width: 100%; font-weight: 800; font-size: 38px; line-height: 44px; color: var(--porch-green); letter-spacing: -.5px; }
</style>
</head>
<body>
  <div class="billboard">
    <svg class="billboard__bands" viewBox="0 0 1150 383" preserveAspectRatio="none" aria-hidden="true">
      <defs>
        <linearGradient id="band-gradient" x1="0" y1="0" x2="1" y2="0">
          <stop offset="0" stop-color="#00b9f0"/>
          <stop offset="1" stop-color="#0096dd"/>
        </linearGradient>
      </defs>
      <polygon points="0,0 926,0 848,292 0,292" fill="#1b1b1b"/>
      <polygon points="0,292 848,292 900,383 0,383" fill="url(#band-gradient)"/>
    </svg>

    <div class="brand-mark" aria-hidden="true"></div>
    <div class="brand-name brand-name__lead">THE CLAIM KEEPER'S</div>
    <span class="rule rule--left"></span>
    <div class="brand-name brand-name__tail">GROUP</div>
    <span class="rule rule--right"></span>

    <div class="service-line">EXPERT PUBLIC ADJUSTERS</div>
    <div class="promise">"MAXIMIZED SETTLEMENT"</div>

    <svg class="phone-icon" viewBox="0 0 60 60" aria-hidden="true">
      <circle cx="30" cy="30" r="30" fill="#d2711f"/>
      <path d="M22 16c2-1 3 0 4 2l2 5c1 2 0 3-1 4l-2 2c1 4 4 7 8 9l2-2c1-1 2-2 4-1l5 2c2 1 3 2 2 4l-1 3c-1 2-3 3-6 2-10-3-17-10-20-20-1-3 0-6 3-10z" fill="#ffffff"/>
    </svg>
    <div class="phone-number">866-FULL CLAIM</div>
    <span class="divider"></span>
    <div class="award">VOTED 2022 BEST<br>PUBLIC ADJUSTER</div>

    <div class="ratings">
      <div class="ratings__grade">A+ Rating</div>
      <div class="ratings__badge" role="img" aria-label="Accredited business badge"></div>
      <div class="ratings__badge-note">QRS Rating: A+</div>
      <div class="ratings__review">Zorbix</div>
      <svg class="ratings__stars" viewBox="0 0 114 20" role="img" aria-label="Five stars">
        <g fill="#f7b500">
          <polygon points="10,0 12.9,6.5 20,7.3 14.7,12 16.2,19 10,15.4 3.8,19 5.3,12 0,7.3 7.1,6.5"/>
          <polygon transform="translate(23.5 0)" points="10,0 12.9,6.5 20,7.3 14.7,12 16.2,19 10,15.4 3.8,19 5.3,12 0,7.3 7.1,6.5"/>
          <polygon transform="translate(47 0)" points="10,0 12.9,6.5 20,7.3 14.7,12 16.2,19 10,15.4 3.8,19 5.3,12 0,7.3 7.1,6.5"/>
          <polygon transform="translate(70.5 0)" points="10,0 12.9,6.5 20,7.3 14.7,12 16.2,19 10,15.4 3.8,19 5.3,12 0,7.3 7.1,6.5"/>
          <polygon transform="translate(94 0)" points="10,0 12.9,6.5 20,7.3 14.7,12 16.2,19 10,15.4 3.8,19 5.3,12 0,7.3 7.1,6.5"/>
        </g>
      </svg>
      <div class="ratings__neighbors">porchline</div>
    </div>
  </div>
</body>
</html>
```